holloway paving service

Needs to have phone number 0418259730 and email markholloway@brightmail.com.au.
ABN 62318470915
name mark holloway

For all your concreting solutions
Excavation
Exposed & colour concrete
House & shed slabs
Driveways
Landing & steps

Contact Information for Business Card

ph 0418259730
email markholloway@brightmail.com.au.
ABN 62318470915
name mark holloway

```html
<!DOCTYPE html>
<html lang="en">
<head>
<meta charset="utf-8">
<title>Holloway Paving Service – Business Card</title>
<link rel="stylesheet" href="https://fonts.googleapis.com/css2?family=Maven+Pro:wght@400;500;700&display=swap">
<style>
  :root {
    --orange: #f06a22;
    --grey: #646464;
    --text-grey: #5a5a5a;
    --white: #ffffff;
    --page: #ececec;
  }
  * { box-sizing: border-box; margin: 0; padding: 0; }
  html, body { width: 1200px; height: 1200px; overflow: hidden; }
  body {
    background: var(--page);
    font-family: "Maven Pro", sans-serif;
    position: relative;
  }
  .card {
    position: absolute;
    left: 150px;
    width: 900px;
    height: 500px;
    background: var(--white);
    box-shadow: 0 6px 18px rgba(0,0,0,0.18);
    overflow: hidden;
  }
  .card--back { top: 70px; }
  .card--front { top: 630px; }

  /* back side */
  .phone-band {
    height: 180px;
    background: var(--grey);
    display: flex;
    flex-direction: column;
    align-items: center;
    justify-content: center;
    gap: 14px;
    color: var(--white);
  }
  .icon-row { display: flex; align-items: center; gap: 22px; }
  .icon-row .rule { width: 90px; height: 2px; background: currentColor; }
  .phone-band .number { font-size: 44px; letter-spacing: 4px; font-weight: 500; }
  .services { padding: 56px 0 0 200px; color: var(--text-grey); }
  .services h2 { font-size: 30px; font-weight: 700; letter-spacing: 0.5px; margin-bottom: 12px; }
  .services ul { list-style: none; }
  .services li {
    font-size: 27px;
    line-height: 32px;
    position: relative;
    padding-left: 32px;
  }
  .services li::before {
    content: "";
    position: absolute;
    left: 2px; top: 11px;
    width: 11px; height: 11px;
    background: var(--orange);
    transform: rotate(45deg);
  }
  .back-strip { position: absolute; left: 0; right: 0; bottom: 0; height: 22px; background: var(--orange); }

  /* front side */
  .brand-area {
    height: 260px;
    display: flex;
    align-items: center;
    justify-content: center;
    gap: 24px;
  }
  .brand-square { width: 46px; height: 46px; background: var(--grey); }
  .brand-name { color: var(--orange); font-size: 38px; font-weight: 700; letter-spacing: 1px; text-transform: uppercase; }
  .contact-band {
    position: absolute;
    left: 0; right: 0; bottom: 0;
    height: 240px;
    background: var(--orange);
    color: var(--white);
    display: flex;
    align-items: center;
    justify-content: space-between;
    padding: 0 70px 0 80px;
  }
  .holder { font-size: 38px; font-weight: 700; letter-spacing: 1.5px; margin-top: 60px; }
  .details { display: flex; flex-direction: column; align-items: center; gap: 8px; }
  .details .icon-row .rule { width: 60px; }
  .details .number { font-size: 28px; letter-spacing: 3px; font-weight: 500; }
  .details .email { font-size: 21px; letter-spacing: 0.5px; }
  .details .abn { font-size: 24px; letter-spacing: 0.5px; }
</style>
</head>
<body>
  <section class="card card--back">
    <div class="phone-band">
      <div class="icon-row">
        <span class="rule"></span>
        <svg class="phone-icon" width="76" height="76" viewBox="0 0 76 76" aria-hidden="true">
          <circle cx="38" cy="38" r="34" fill="none" stroke="#fff" stroke-width="4"/>
          <path d="M28 20c3-2 5-1 6 2l3 7c1 2 0 4-2 5l-2 1c1 5 5 10 10 12l1-2c1-2 3-3 5-2l7 3c3 1 3 4 1 6-3 4-7 5-12 3-9-4-17-12-20-22-1-5 0-10 3-13z" fill="none" stroke="#fff" stroke-width="3.5" stroke-linejoin="round"/>
        </svg>
        <span class="rule"></span>
      </div>
      <div class="number">0418259730</div>
    </div>
    <div class="services">
      <h2>For all your concreting solutions</h2>
      <ul>
        <li>Excavation</li>
        <li>Exposed &amp; colour concrete</li>
        <li>House &amp; shed slabs</li>
        <li>Driveways</li>
        <li>Landing &amp; steps</li>
      </ul>
    </div>
    <div class="back-strip"></div>
  </section>

  <section class="card card--front">
    <div class="brand-area">
      <span class="brand-square"></span>
      <span class="brand-name">Holloway Paving Service</span>
    </div>
    <div class="contact-band">
      <div class="holder">Mark Holloway</div>
      <div class="details">
        <div class="icon-row">
          <span class="rule"></span>
          <svg class="phone-icon" width="50" height="50" viewBox="0 0 76 76" aria-hidden="true">
            <circle cx="38" cy="38" r="34" fill="none" stroke="#fff" stroke-width="5"/>
            <path d="M28 20c3-2 5-1 6 2l3 7c1 2 0 4-2 5l-2 1c1 5 5 10 10 12l1-2c1-2 3-3 5-2l7 3c3 1 3 4 1 6-3 4-7 5-12 3-9-4-17-12-20-22-1-5 0-10 3-13z" fill="none" stroke="#fff" stroke-width="4.5" stroke-linejoin="round"/>
          </svg>
          <span class="rule"></span>
        </div>
        <div class="number">0418259730</div>
        <div class="email">markholloway@brightmail.com.au.</div>
        <div class="abn">ABN 62318470915</div>
      </div>
    </div>
  </section>
</body>
</html>
```